Maple Roster Business Card for recruitment company

We are looking for a Business Card Design that incorporates our personal details and our busines name and logo. We are a specialized search consultancy that recruit Property and Construction professionals.
We would like a business card that stands out and is appealing to the Construction and Property industry as well.

Target Market(s)

people in the construction and property industry

Contact Information for Business Card

Business Name and logo

Font styles to use
Serif

Colors
0094D4
00A9DD
6FCCEA
C7EBF8
E9F6FB

Requirements
Must have
• Business name and logo as well as contact details
Should not have
• No photos of us please

```html
<!DOCTYPE html>
<html lang="en">
<head>
<meta charset="utf-8">
<title>Maple Roster Business Card</title>
<link rel="stylesheet" href="https://fonts.googleapis.com/css2?family=Josefin+Sans:wght@300;400&family=Arimo:wght@400&display=swap">
<style>
  :root {
    --backdrop: #8e8e8e;
    --ink-teal: #023a4f;
    --paper: #ffffff;
    --shadow: rgba(0, 0, 0, 0.55);
  }
  * { margin: 0; padding: 0; box-sizing: border-box; }
  html, body {
    width: 1075px;
    height: 1200px;
    overflow: hidden;
    background: var(--backdrop);
  }
  .canvas { position: relative; width: 1075px; height: 1200px; }
  .card {
    position: absolute;
    width: 664px;
    height: 396px;
    box-shadow: 3px 3px 2px var(--shadow);
  }
  .card-front { left: 206px; top: 187px; background: var(--ink-teal); color: var(--paper); }
  .card-back { left: 203px; top: 637px; background: var(--paper); }

  .holder { position: absolute; left: 35px; top: 52px; }
  .holder-name {
    font-family: "Josefin Sans", sans-serif;
    font-weight: 400;
    font-size: 28px;
    letter-spacing: 0.2px;
    line-height: 1;
  }
  .holder-role {
    font-family: "Arimo", sans-serif;
    font-size: 18px;
    margin-top: 2px;
  }
  .address {
    position: absolute; left: 36px; top: 180px;
    font-family: "Arimo", sans-serif;
    font-size: 18px;
    line-height: 23.5px;
  }
  .contacts {
    position: absolute; left: 35px; top: 277px;
    list-style: none;
    font-family: "Arimo", sans-serif;
    font-size: 18px;
    line-height: 23.5px;
  }
  .contacts li { display: flex; align-items: center; gap: 5px; }
  .contacts svg { width: 17px; height: 17px; flex: none; }

  .front-brand {
    position: absolute; left: 330px; top: 196px; width: 310px;
    text-align: center;
    font-family: "Josefin Sans", sans-serif;
    font-weight: 400;
    font-size: 30px;
    letter-spacing: 3px;
    color: var(--paper);
  }
  .back-brand {
    position: absolute; left: 0; right: 0; top: 168px;
    text-align: center;
    font-family: "Josefin Sans", sans-serif;
    font-weight: 300;
    font-size: 50px;
    letter-spacing: 1px;
    color: var(--ink-teal);
  }
</style>
</head>
<body>
<main class="canvas">
  <section class="card card-front">
    <div class="holder">
      <div class="holder-name">DANIEL HART</div>
      <div class="holder-role">Managing Director</div>
    </div>
    <address class="address" style="font-style:normal">
      421, Address line<br>goes here<br>45452,Country Name
    </address>
    <ul class="contacts">
      <li>
        <svg viewBox="0 0 24 24" aria-hidden="true"><path fill="#fff" d="M6.6 2.5l3 3.6-1.9 2.2c1.2 2.6 3.3 4.7 5.9 5.9l2.2-1.9 3.6 3-1.6 3.2C10.5 18.9 5.1 13.5 3.4 4.1z"/><path d="M14 3a7 7 0 0 1 7 7M14 6.5a3.5 3.5 0 0 1 3.5 3.5" fill="none" stroke="#fff" stroke-width="1.8"/></svg>
        044-123 456 789
      </li>
      <li>
        <svg viewBox="0 0 24 24" aria-hidden="true"><rect x="2" y="5" width="20" height="14" fill="#fff"/><path d="M2 5l10 8 10-8" fill="none" stroke="#023a4f" stroke-width="1.6"/></svg>
        info@webname.com
      </li>
      <li>
        <svg viewBox="0 0 24 24" aria-hidden="true"><g fill="none" stroke="#fff" stroke-width="1.8"><circle cx="12" cy="12" r="9.5"/><ellipse cx="12" cy="12" rx="4" ry="9.5"/><path d="M2.5 12h19M4 7h16M4 17h16"/></g></svg>
        www.websitename.com
      </li>
    </ul>
    <div class="front-brand">MAPLE ROSTER</div>
  </section>

  <section class="card card-back">
    <div class="back-brand">MAPLE ROSTER</div>
  </section>
</main>
</body>
</html>
```